Vantoq Business Card Project showing the logo and a marbo image on the rear

Design a whacky but professional business card, the logo is for the front and the Marbo image is for the rear. Happy to consider other open source Marbo Images if the designer wants to select one from the web. Vantoq is a competitor to OMB.com.au and Pellory.com.au and is based around every property in Australia

Target Market(s)

Business

Contact Information for Business Card

Name, Title, Email, Web, Phone Number

Font styles to use
Other font styles liked:
• avenir

Requirements
Must have
• Image on Back logo on front
Nice to have
• Happy to consider other images on rear, preftably Colin Marbo. Image supplied I own, we can use open source other Marbo Images

```html
<!DOCTYPE html>
<html lang="en">
<head>
<meta charset="utf-8">
<title>Vantoq Business Card</title>
<link rel="stylesheet" href="https://fonts.googleapis.com/css2?family=Nunito+Sans:wght@700;800&family=Roboto:wght@400&display=swap">
<style>
  :root {
    --stage: #1e1e1e;
    --card-white: #f1f1f1;
    --ink: #151515;
    --orange: #e8800c;
    --art-orange: #ef8a12;
    --art-night: #3a3a3c;
    --art-green: #8cc43c;
  }
  * { margin: 0; padding: 0; box-sizing: border-box; }
  html, body { width: 1200px; height: 1138px; overflow: hidden; }
  body { background: var(--stage); position: relative; font-family: "Roboto", Arial, sans-serif; color: var(--ink); }

  .card {
    position: absolute;
    border-radius: 14px;
    overflow: hidden;
  }
  .card-back {
    left: 274px; top: 185px; width: 623px; height: 377px;
    background: linear-gradient(90deg, var(--art-orange) 0%, var(--art-orange) 49%, var(--art-night) 51%, var(--art-night) 100%);
  }
  .card-back .art-ground {
    position: absolute; left: 0; right: 0; bottom: 0; height: 48%;
    background: linear-gradient(180deg, rgba(214,72,140,0.55) 0%, rgba(90,170,210,0.55) 60%, var(--art-green) 100%);
  }

  .card-front {
    left: 276px; top: 607px; width: 618px; height: 375px;
    background: linear-gradient(160deg, #f7f7f7 0%, var(--card-white) 60%, #e4e4e4 100%);
  }
  .brand { position: absolute; left: 30px; top: 40px; display: flex; align-items: center; gap: 30px; }
  .brand-mark { width: 64px; height: 64px; background: var(--orange); }
  .brand-name { font-family: "Nunito Sans", Arial, sans-serif; font-weight: 800; font-size: 78px; line-height: 1; letter-spacing: 1px; color: var(--ink); }

  .address { position: absolute; left: 30px; top: 168px; font-size: 16px; }
  .contacts { position: absolute; left: 34px; top: 204px; list-style: none; }
  .contacts li { display: flex; align-items: center; height: 24px; font-size: 16.5px; }
  .contacts svg { width: 14px; height: 14px; margin-right: 17px; }
  .accent { color: var(--orange); }

  .swoosh { position: absolute; left: 0; bottom: 0; width: 618px; height: 375px; }
  .person { position: absolute; right: 40px; top: 297px; text-align: right; }
  .person-name { font-family: "Nunito Sans", Arial, sans-serif; font-weight: 700; font-size: 25px; line-height: 1.1; }
  .person-title { font-size: 16px; margin-top: 2px; }
</style>
</head>
<body>
  <div class="card card-back" role="img" aria-label="Colourful hand-drawn city artwork: cartoon buildings under a sunny orange sky and a starry night sky, with a train along the bottom">
    <div class="art-ground"></div>
  </div>

  <div class="card card-front">
    <svg class="swoosh" viewBox="0 0 618 375" aria-hidden="true">
      <path d="M0 322 C120 330 220 330 330 300 C450 268 540 258 618 262 L618 375 L0 375 Z" fill="var(--orange)"/>
      <path d="M0 290 C60 330 150 345 260 320 C380 292 480 236 618 244 L618 256 C480 252 390 302 270 334 C160 360 60 340 0 305 Z" fill="var(--ink)"/>
      <path d="M60 320 C140 342 220 340 300 318" stroke="var(--ink)" stroke-width="2" fill="none"/>
    </svg>

    <div class="brand">
      <div class="brand-mark"></div>
      <div class="brand-name">Vantoq</div>
    </div>

    <p class="address">Level 7, 48 Corran Street, Sydney 2000, Australia</p>

    <ul class="contacts">
      <li>
        <svg viewBox="0 0 16 16"><circle cx="8" cy="8" r="7" fill="none" stroke="var(--orange)" stroke-width="1.5"/><path d="M5.5 4.5 L7 6 L6.2 7.2 C6.8 8.4 7.6 9.2 8.8 9.8 L10 9 L11.5 10.5 L10.5 11.8 C7.5 11.5 4.5 8.5 4.2 5.5 Z" fill="var(--orange)"/></svg>
        (00) 4815 2930
      </li>
      <li>
        <svg viewBox="0 0 16 16"><rect x="1" y="3" width="14" height="10" fill="var(--orange)"/><path d="M1 3 L8 9 L15 3" stroke="#fff" stroke-width="1.3" fill="none"/></svg>
        dalton@vantoq.com
      </li>
      <li>
        <svg viewBox="0 0 16 16"><circle cx="8" cy="8" r="7" fill="var(--orange)"/><path d="M1 8 H15 M8 1 C4 5 4 11 8 15 M8 1 C12 5 12 11 8 15" stroke="#fff" stroke-width="1" fill="none"/></svg>
        www.<span class="accent">vantoq</span>.com
      </li>
    </ul>

    <div class="person">
      <div class="person-name">Ira Dalton</div>
      <div class="person-title">Founder &amp; CEO</div>
    </div>
  </div>
</body>
</html>
```